BRIGHT RIVER POWER.

I'd like my business logo.
contact name: Dennis Halvorsen
phone:0438759164
email: info@brightriverpower.net.au
website: www.brightriverpower.net.au

services:
solar
battery storage
LED lighting
energy saving solutions
general electrical
I'd like the design to look professional

Target Market(s)

Everyone

Industry/Entity Type

Business

Contact Information for Business Card

as described above

Requirements
Must have
• Id like the colours and the design to work well with my logo.

```html
<!DOCTYPE html>
<html lang="en">
<head>
<meta charset="utf-8">
<title>Bright River Power – Business Card</title>
<link href="https://fonts.googleapis.com/css2?family=Montserrat:wght@400;500;700&display=swap" rel="stylesheet">
<style>
  :root {
    --bg: #e8e5df;
    --card-white: #ffffff;
    --card-black: #111111;
    --green: #3fae49;
    --lime: #8dc63f;
    --orange: #f39a1e;
    --amber: #f7b52c;
    --text-green: #3b9a45;
  }
  * { margin: 0; padding: 0; box-sizing: border-box; }
  html, body { width: 1200px; height: 1022px; overflow: hidden; }
  body {
    background: var(--bg);
    font-family: "Montserrat", sans-serif;
    position: relative;
  }
  .card {
    position: absolute;
    left: 220px;
    width: 760px;
    height: 434px;
    border-radius: 18px;
    overflow: hidden;
    box-shadow: 0 10px 30px rgba(0,0,0,0.18);
  }
  .card-front { top: 56px; background: var(--card-white); }
  .card-back { top: 532px; background: var(--card-black); }

  .front-panel { position: absolute; inset: 0; }

  .panel-mark {
    position: absolute;
    left: 40px;
    top: 167px;
    width: 100px;
    height: 100px;
    border-radius: 50%;
    background: var(--amber);
  }

  .brand {
    position: absolute;
    left: 360px;
    top: 46px;
    display: flex;
    align-items: center;
    gap: 14px;
  }
  .brand-dot {
    width: 34px; height: 34px; border-radius: 50%;
    background: var(--amber);
  }
  .brand-name {
    font-weight: 700;
    font-size: 34px;
    letter-spacing: 1px;
    color: var(--green);
  }

  .contact {
    position: absolute;
    left: 360px;
    top: 130px;
  }
  .contact-name {
    font-weight: 700;
    font-size: 28px;
    color: var(--orange);
    margin-bottom: 14px;
  }
  .contact-line {
    display: flex;
    align-items: center;
    gap: 10px;
    font-size: 17px;
    color: var(--text-green);
    margin-bottom: 10px;
  }
  .contact-line svg { width: 16px; height: 16px; flex: none; }

  .services {
    position: absolute;
    left: 360px;
    top: 300px;
    list-style: none;
    display: grid;
    grid-template-columns: auto auto;
    column-gap: 40px;
    row-gap: 10px;
  }
  .services li {
    display: flex;
    align-items: center;
    gap: 10px;
    font-size: 17px;
    color: var(--text-green);
  }
  .services li::before {
    content: "";
    width: 8px; height: 8px; border-radius: 50%;
    background: var(--orange);
  }

  .back-brand {
    position: absolute;
    inset: 0;
    display: flex;
    align-items: center;
    justify-content: center;
    gap: 24px;
  }
  .back-dot {
    width: 80px; height: 80px; border-radius: 50%;
    background: var(--amber);
  }
  .back-name {
    font-weight: 700;
    font-size: 42px;
    letter-spacing: 1px;
    color: var(--lime);
  }
</style>
</head>
<body>

  <section class="card card-front">
    <svg class="front-panel" viewBox="0 0 760 434" width="760" height="434" aria-hidden="true">
      <path d="M0 0 H232 Q330 217 232 434 H0 Z" fill="var(--lime)"/>
      <path d="M0 0 H210 Q306 217 210 434 H0 Z" fill="var(--green)"/>
      <path d="M0 0 H196 Q290 217 196 434 H0 Z" fill="var(--card-black)"/>
    </svg>
    <div class="panel-mark"></div>

    <div class="brand">
      <span class="brand-dot"></span>
      <span class="brand-name">BRIGHT RIVER POWER</span>
    </div>

    <div class="contact">
      <p class="contact-name">Dennis Halvorsen</p>
      <p class="contact-line">
        <svg viewBox="0 0 16 16"><path d="M4 1 L6.5 4 L5 6 Q6.5 9.5 10 11 L12 9.5 L15 12 L13 15 Q5 14 1 3 Z" fill="var(--orange)"/></svg>
        0438759164
      </p>
      <p class="contact-line">
        <svg viewBox="0 0 16 16"><rect x="1" y="3" width="14" height="10" rx="1.5" fill="none" stroke="var(--orange)" stroke-width="1.6"/><path d="M1.5 4 L8 9 L14.5 4" fill="none" stroke="var(--orange)" stroke-width="1.6"/></svg>
        info@brightriverpower.net.au
      </p>
      <p class="contact-line">
        <svg viewBox="0 0 16 16"><circle cx="8" cy="8" r="6.5" fill="none" stroke="var(--orange)" stroke-width="1.5"/><ellipse cx="8" cy="8" rx="3" ry="6.5" fill="none" stroke="var(--orange)" stroke-width="1.2"/><path d="M1.5 8 H14.5" stroke="var(--orange)" stroke-width="1.2"/></svg>
        www.brightriverpower.net.au
      </p>
    </div>

    <ul class="services">
      <li>Solar</li>
      <li>LED lighting</li>
      <li>Battery storage</li>
      <li>Energy saving solutions</li>
    </ul>
  </section>

  <section class="card card-back">
    <div class="back-brand">
      <span class="back-dot"></span>
      <span class="back-name">BRIGHT RIVER POWER</span>
    </div>
  </section>

</body>
</html>
```